Upmarket Dessert Lounge needs a Business Card Design

We are an upmarket dessert lounge needing a business card to match our image.

We want something that is simple yet beautiful, feminine, classy, sophisticated and elegant. We want it to stand out and don't mind if it is bold.

The design should include our logo and colours of red or maroon with gold highlights. We don't mind if black is used.

Marlow & Quince

Target Market(s)

For those who like to indulge or treat themselves and give in to their temptations on good quality desserts.

Industry/Entity Type

Business

Requirements
Must have
• Must include our logo and our name

Marlow & Quince

M & Q

```html
<!DOCTYPE html>
<html lang="en">
<head>
<meta charset="utf-8">
<title>Marlow &amp; Quince — Business Card</title>
<link href="https://fonts.googleapis.com/css2?family=Open+Sans:wght@400;600;700&display=swap" rel="stylesheet">
<style>
  :root {
    --maroon: #7b1416;
    --maroon-deep: #6a1012;
    --gold: #fbd3a0;
    --cream: #fcd9a8;
    --white: #ffffff;
    --ink: #333333;
    --backdrop: #d9d9d9;
  }
  * { margin: 0; padding: 0; box-sizing: border-box; }
  html, body {
    width: 956px; height: 1200px; overflow: hidden;
    background: var(--backdrop);
    font-family: "Open Sans", Arial, sans-serif;
  }
  .canvas { position: relative; width: 956px; height: 1200px; }

  .card {
    position: absolute;
    width: 798px; height: 456px;
    border-radius: 28px;
    overflow: hidden;
  }
  .card-front { left: 79px; top: 70px; background: var(--white); }
  .card-back { left: 73px; top: 632px; background: var(--maroon); }

  .front-wave { position: absolute; left: 0; top: 0; width: 798px; height: 456px; }

  .brand-name {
    position: absolute;
    left: 52px; top: 145px;
    width: 330px;
    text-align: center;
    font-size: 30px; font-weight: 600;
    letter-spacing: 1px;
    color: var(--maroon);
    text-transform: uppercase;
  }

  .contact { position: absolute; left: 475px; top: 60px; color: var(--ink); }
  .contact-name { font-size: 21px; font-weight: 700; line-height: 28px; }
  .contact-role { font-size: 21px; font-weight: 400; line-height: 26px; letter-spacing: 0.5px; }
  .contact-list { list-style: none; margin-top: 14px; font-size: 18px; line-height: 30px; }
  .contact-list.web { margin-top: 4px; }
  .contact-list b { font-weight: 700; }

  .address {
    position: absolute; left: 40px; top: 410px;
    font-size: 20px; color: var(--white);
  }

  .monogram {
    position: absolute; left: 0; top: 0;
    width: 798px; height: 456px;
    display: flex; align-items: center; justify-content: center;
    font-size: 96px; font-weight: 600;
    color: var(--cream);
  }
</style>
</head>
<body>
<main class="canvas">
  <section class="card card-front">
    <svg class="front-wave" viewBox="0 0 798 456" aria-hidden="true">
      <path d="M170 322 C 330 300, 480 395, 600 385 C 690 378, 760 350, 798 325 L 798 342 C 760 365, 690 392, 600 398 C 480 405, 330 325, 170 322 Z" fill="var(--gold)"/>
      <path d="M0 365 C 80 340, 160 322, 250 330 C 380 345, 480 400, 600 400 C 690 400, 760 370, 798 350 L 798 456 L 0 456 Z" fill="var(--maroon)"/>
    </svg>
    <p class="brand-name">Marlow &amp; Quince</p>
    <div class="contact">
      <p class="contact-name">Your Name</p>
      <p class="contact-role">Designation</p>
      <ul class="contact-list">
        <li><b>p</b> : 123-456-7890</li>
        <li><b>c</b> : 123-456-7890</li>
        <li><b>f</b> : 123-456-7890</li>
      </ul>
      <ul class="contact-list web">
        <li><b>e</b> : name@yourwebsite.com</li>
        <li><b>w</b> : www.marlow&amp;quince.com</li>
      </ul>
    </div>
    <p class="address">0000, Street Name, City Name, Country Code.</p>
  </section>

  <section class="card card-back">
    <p class="monogram">M &amp; Q</p>
  </section>
</main>
</body>
</html>
```